Boutique Technology Consultancy specialising is Electronic and physical security

We need to redo our existing outdated website. For your reference the link www.pelu.com.au

```html
<!DOCTYPE html>
<html lang="en">
<head>
<meta charset="utf-8">
<title>PELU Services</title>
<link href="https://fonts.googleapis.com/css2?family=Outfit:wght@300;400;500;600;700;800&display=swap" rel="stylesheet">
<style>
:root{
  --bg:#231f20;
  --bg-deep:#1b1819;
  --red:#d7261e;
  --red-dark:#8e1812;
  --white:#ffffff;
  --muted:#c9c5c4;
  --line:#7a2320;
}
*{margin:0;padding:0;box-sizing:border-box}
html,body{width:1200px;height:3708px;overflow:hidden}
body{background:var(--bg);color:var(--white);font-family:'Outfit',sans-serif;position:relative}
.abs{position:absolute}
.brand{font-weight:700;font-size:44px;letter-spacing:1px;display:flex;align-items:center;gap:10px;color:var(--white)}
.brand .dot{width:14px;height:14px;background:var(--red)}
.nav-link{font-size:16px;top:48px;color:var(--white)}
.nav-link.active{border-bottom:2px solid var(--red);padding-bottom:3px}
.hero{left:0;top:113px;width:1200px;height:600px;background:radial-gradient(ellipse at 60% 40%,#5a3a2c 0%,#3a2a26 35%,#1f2326 75%,#151719 100%)}
.hero-title{left:0;top:330px;width:1200px;text-align:center;font-weight:800;font-size:56px;line-height:80px;text-transform:uppercase}
.btn{background:var(--red);color:var(--white);font-weight:600;font-size:15px;display:flex;align-items:center;justify-content:center;gap:8px}
.btn svg{width:16px;height:12px}
.slide-dash{top:683px;width:30px;height:3px;background:#9b9696}
.slide-dash.on{background:var(--red)}
.section-title{font-weight:800;font-size:36px;text-transform:uppercase;text-align:center;width:1200px;left:0}
.underline{height:3px;background:var(--red)}
.divider{left:112px;width:977px;height:1px;background:var(--line)}
.photo{background:linear-gradient(135deg,#6e6e6e,#2c2c2c)}
.about-text{left:675px;top:938px;width:414px;font-size:16px;line-height:30px;text-align:justify;font-weight:300}
.check-list{left:675px;top:1048px;list-style:none;font-size:17px;font-weight:300}
.check-list li{display:flex;align-items:center;gap:12px;height:33px}
.chev{width:18px;height:14px;flex:none}
.team-card{top:1526px;width:307px;text-align:center}
.team-photo{height:300px;background:linear-gradient(160deg,#6b5444,#3a3431 60%,#222)}
.team-name{font-size:25px;font-weight:500;margin-top:22px}
.team-role{font-size:18px;font-weight:300;margin-top:2px}
.team-desc{font-size:13px;font-weight:300;color:var(--muted);line-height:21px;margin-top:12px;padding:0 10px}
.arrow-circle{width:36px;height:36px;border:1.5px solid var(--red);border-radius:50%;display:flex;align-items:center;justify-content:center}
.lead{left:0;width:1200px;text-align:center;font-size:16px;line-height:26px;font-weight:300}
.svc{width:300px}
.svc-title{font-size:30px;font-weight:500;line-height:39px;margin-top:30px}
.svc-list{list-style:none;font-size:15px;font-weight:300;margin-top:12px}
.svc-list li{display:flex;align-items:center;gap:8px;height:23px}
.svc-list svg{width:11px;height:10px;flex:none}
.svc .btn{width:137px;height:42px;margin-top:24px}
.exp-card{top:2930px;width:226px}
.exp-img{height:212px;position:relative;background:linear-gradient(170deg,#d8d8d8,#6a6a6a 55%,#2a2a2a)}
.exp-label{position:absolute;left:0;bottom:0;width:100%;height:43px;background:linear-gradient(90deg,var(--red) 55%,var(--red-dark));clip-path:polygon(0 0,88% 0,100% 100%,0 100%);font-size:16px;font-weight:600;display:flex;align-items:center;padding-left:15px}
.exp-desc{font-size:12px;font-weight:300;color:var(--muted);line-height:20px;margin-top:22px;text-align:justify}
.footer{left:0;top:3356px;width:1200px;height:352px;background:var(--bg-deep)}
.foot-head{font-size:16px;font-weight:500;top:3455px}
.foot-line{top:3483px;width:82px;height:2px;background:var(--red)}
.foot-text{font-size:15px;font-weight:300;line-height:28px}
.social{width:50px;height:50px;border:2px solid var(--red);border-radius:50%;display:flex;align-items:center;justify-content:center;font-size:10px;font-weight:500}
</style>
</head>
<body>

<!-- Header -->
<div class="abs brand" style="left:112px;top:34px"><span class="dot"></span>PELU</div>
<a class="abs nav-link active" style="left:409px">Home</a>
<a class="abs nav-link" style="left:492px">Experience</a>
<a class="abs nav-link" style="left:614px">Services</a>
<a class="abs nav-link" style="left:712px">Team</a>
<a class="abs nav-link" style="left:792px">About</a>
<a class="abs nav-link" style="left:877px">Contact</a>
<svg class="abs" style="left:990px;top:48px" width="20" height="20" viewBox="0 0 20 20" fill="none" stroke="#d7261e" stroke-width="2"><circle cx="8" cy="8" r="6"/><line x1="13" y1="13" x2="18" y2="18"/></svg>
<svg class="abs" style="left:1028px;top:46px" width="20" height="22" viewBox="0 0 20 22" fill="none" stroke="#d7261e" stroke-width="2"><circle cx="10" cy="6" r="5"/><path d="M2 21v-3a6 6 0 0 1 6-6h4a6 6 0 0 1 6 6v3z"/></svg>
<svg class="abs" style="left:1066px;top:47px" width="24" height="22" viewBox="0 0 24 22" fill="none" stroke="#d7261e" stroke-width="2"><path d="M1 2h4l3 12h12l3-9H7"/><circle cx="9" cy="19" r="2"/><circle cx="19" cy="19" r="2"/></svg>

<!-- Hero -->
<div class="abs hero" role="img" aria-label="Photo of a modern retail technology store interior with warm orange lighting"></div>
<h1 class="abs hero-title">Your technology projects<br>made easy</h1>
<a class="abs btn" style="left:528px;top:520px;width:144px;height:43px">Get Started <svg viewBox="0 0 16 12" fill="none" stroke="#fff" stroke-width="2"><path d="M0 6h14M9 1l5 5-5 5"/></svg></a>
<div class="abs slide-dash" style="left:543px"></div>
<div class="abs slide-dash on" style="left:586px"></div>
<div class="abs slide-dash" style="left:629px"></div>

<!-- About -->
<div class="abs photo" style="left:112px;top:823px;width:438px;height:447px;border-radius:6px" role="img" aria-label="Black and white photo of server racks with network cabling"></div>
<h2 class="abs" style="left:676px;top:848px;font-size:36px;font-weight:800">ABOUT US</h2>
<div class="abs underline" style="left:641px;top:902px;width:102px"></div>
<p class="abs about-text">PELU Services was established in 2016 by Rob Hartley to provide technology consulting services to corporate and government clients with a focus on:</p>
<ul class="abs check-list">
  <li><svg class="chev" viewBox="0 0 18 14" fill="none" stroke="#d7261e" stroke-width="2.5"><path d="M3 2l6 5-6 5M10 2l6 5-6 5"/></svg>Property/facilities management</li>
  <li><svg class="chev" viewBox="0 0 18 14" fill="none" stroke="#d7261e" stroke-width="2.5"><path d="M3 2l6 5-6 5M10 2l6 5-6 5"/></svg>Asset management</li>
  <li><svg class="chev" viewBox="0 0 18 14" fill="none" stroke="#d7261e" stroke-width="2.5"><path d="M3 2l6 5-6 5M10 2l6 5-6 5"/></svg>Development and Construction</li>
</ul>
<a class="abs btn" style="left:675px;top:1182px;width:136px;height:43px">Learn More <svg viewBox="0 0 16 12" fill="none" stroke="#fff" stroke-width="2"><path d="M0 6h14M9 1l5 5-5 5"/></svg></a>

<div class="abs divider" style="top:1363px"></div>

<!-- Team -->
<h2 class="abs section-title" style="top:1422px">Our Team</h2>
<div class="abs underline" style="left:555px;top:1476px;width:90px"></div>
<div class="abs arrow-circle" style="left:63px;top:1659px"><svg width="10" height="14" viewBox="0 0 10 14" fill="none" stroke="#fff" stroke-width="2"><path d="M8 1L2 7l6 6"/></svg></div>
<div class="abs arrow-circle" style="left:1104px;top:1659px"><svg width="10" height="14" viewBox="0 0 10 14" fill="none" stroke="#fff" stroke-width="2"><path d="M2 1l6 6-6 6"/></svg></div>

<div class="abs team-card" style="left:112px">
  <div class="team-photo" role="img" aria-label="Portrait photo of Rob Hartley"></div>
  <div class="team-name">Rob Hartley</div>
  <div class="team-role">Principal Consultant</div>
  <p class="team-desc">Rob founded PELU in 2016 and continues to lead the organisation nationally.</p>
</div>
<div class="abs team-card" style="left:447px">
  <div class="team-photo" role="img" aria-label="Portrait photo of Simon Keller"></div>
  <div class="team-name">Simon Keller</div>
  <div class="team-role">Principal Consultant</div>
  <p class="team-desc">Simon founded Norfield Group in 2016 and joined PELU as a Director in 2022, taking over leadership of the NSW office.</p>
</div>
<div class="abs team-card" style="left:781px">
  <div class="team-photo" role="img" aria-label="Portrait photo of Daniel Morrow"></div>
  <div class="team-name">Daniel Morrow</div>
  <div class="team-role">Senior Consultant</div>
  <p class="team-desc">Daniel established PELU's Queensland office in 2019 and leads all of PELU's engagements in the northern states.</p>
</div>

<div class="abs divider" style="top:2066px"></div>

<!-- Services -->
<h2 class="abs section-title" style="top:2125px">Our Services</h2>
<p class="abs lead" style="top:2210px">PELU Services provides independent professional services for projects as well as operations and<br>maintenance. We offer end to end services including</p>

<div class="abs svc" style="left:183px;top:2310px">
  <svg width="58" height="56" viewBox="0 0 58 56" fill="none" stroke="#d7261e" stroke-width="2"><circle cx="20" cy="16" r="9"/><circle cx="20" cy="16" r="3"/><path d="M30 30l12-12M38 16h6v6"/><rect x="4" y="34" width="20" height="16"/><path d="M30 50h22M36 36h14v8H36z"/></svg>
  <div class="svc-title">Strategy</div>
  <ul class="svc-list">
    <li><svg viewBox="0 0 11 10" fill="none" stroke="#d7261e" stroke-width="2"><path d="M1 1l4 4-4 4M6 1l4 4-4 4"/></svg>Technology roadmaps</li>
    <li><svg viewBox="0 0 11 10" fill="none" stroke="#d7261e" stroke-width="2"><path d="M1 1l4 4-4 4M6 1l4 4-4 4"/></svg>Master standards</li>
    <li><svg viewBox="0 0 11 10" fill="none" stroke="#d7261e" stroke-width="2"><path d="M1 1l4 4-4 4M6 1l4 4-4 4"/></svg>Asset management plans</li>
  </ul>
  <a class="btn">Learn More <svg viewBox="0 0 16 12" fill="none" stroke="#fff" stroke-width="2"><path d="M0 6h14M9 1l5 5-5 5"/></svg></a>
</div>

<div class="abs svc" style="left:500px;top:2310px">
  <svg width="56" height="56" viewBox="0 0 56 56" fill="none" stroke="#d7261e" stroke-width="2"><rect x="4" y="6" width="40" height="46"/><path d="M4 14h6M4 22h6M16 30h20v16H16zM26 30v16M16 38h10"/><path d="M34 24l16-16 4 4-16 16-6 2z"/></svg>
  <div class="svc-title">Projects</div>
  <ul class="svc-list">
    <li><svg viewBox="0 0 11 10" fill="none" stroke="#d7261e" stroke-width="2"><path d="M1 1l4 4-4 4M6 1l4 4-4 4"/></svg>Audit</li>
    <li><svg viewBox="0 0 11 10" fill="none" stroke="#d7261e" stroke-width="2"><path d="M1 1l4 4-4 4M6 1l4 4-4 4"/></svg>Design</li>
    <li><svg viewBox="0 0 11 10" fill="none" stroke="#d7261e" stroke-width="2"><path d="M1 1l4 4-4 4M6 1l4 4-4 4"/></svg>Procurement</li>
    <li><svg viewBox="0 0 11 10" fill="none" stroke="#d7261e" stroke-width="2"><path d="M1 1l4 4-4 4M6 1l4 4-4 4"/></svg>Technical project management</li>
    <li><svg viewBox="0 0 11 10" fill="none" stroke="#d7261e" stroke-width="2"><path d="M1 1l4 4-4 4M6 1l4 4-4 4"/></svg>Witness testing</li>
  </ul>
  <a class="btn">Learn More <svg viewBox="0 0 16 12" fill="none" stroke="#fff" stroke-width="2"><path d="M0 6h14M9 1l5 5-5 5"/></svg></a>
</div>

<div class="abs svc" style="left:809px;top:2310px">
  <svg width="62" height="60" viewBox="0 0 62 60" fill="none" stroke="#d7261e" stroke-width="2"><circle cx="24" cy="24" r="14"/><circle cx="24" cy="24" r="6"/><path d="M24 4v6M24 38v6M4 24h6M38 24h6M10 10l4 4M34 34l4 4M38 10l-4 4M10 38l4-4"/><circle cx="46" cy="44" r="8"/><circle cx="46" cy="44" r="3"/></svg>
  <div class="svc-title">Operations &amp;<br>maintenance</div>
  <ul class="svc-list">
    <li><svg viewBox="0 0 11 10" fill="none" stroke="#d7261e" stroke-width="2"><path d="M1 1l4 4-4 4M6 1l4 4-4 4"/></svg>Service &amp; maintenance specifications</li>
    <li><svg viewBox="0 0 11 10" fill="none" stroke="#d7261e" stroke-width="2"><path d="M1 1l4 4-4 4M6 1l4 4-4 4"/></svg>Policies and procedures</li>
    <li><svg viewBox="0 0 11 10" fill="none" stroke="#d7261e" stroke-width="2"><path d="M1 1l4 4-4 4M6 1l4 4-4 4"/></svg>Procurement; and</li>
    <li><svg viewBox="0 0 11 10" fill="none" stroke="#d7261e" stroke-width="2"><path d="M1 1l4 4-4 4M6 1l4 4-4 4"/></svg>Service reviews</li>
  </ul>
  <a class="btn">Learn More <svg viewBox="0 0 16 12" fill="none" stroke="#fff" stroke-width="2"><path d="M0 6h14M9 1l5 5-5 5"/></svg></a>
</div>

<div class="abs divider" style="top:2698px"></div>

<!-- Experience -->
<h2 class="abs section-title" style="top:2752px">Our Experience</h2>
<div class="abs underline" style="left:555px;top:2803px;width:90px"></div>
<p class="abs lead" style="top:2834px">PELU has a diverse range of project experience across a range of industries within both the public and private<br>sectors. The following is a small sample of some of the clients and sites we have worked with.</p>
<div class="abs arrow-circle" style="left:63px;top:3020px"><svg width="10" height="14" viewBox="0 0 10 14" fill="none" stroke="#fff" stroke-width="2"><path d="M8 1L2 7l6 6"/></svg></div>
<div class="abs arrow-circle" style="left:1104px;top:3020px"><svg width="10" height="14" viewBox="0 0 10 14" fill="none" stroke="#fff" stroke-width="2"><path d="M2 1l6 6-6 6"/></svg></div>

<div class="abs exp-card" style="left:112px">
  <div class="exp-img" role="img" aria-label="Black and white photo of a shopping centre glass dome"><div class="exp-label">Harbour Central</div></div>
  <p class="exp-desc">Security technology design consulting for this popular retail and entertainment hub which is managed by the Crestline Group.</p>
</div>
<div class="abs exp-card" style="left:362px">
  <div class="exp-img" role="img" aria-label="Black and white photo of a motorway overpass"><div class="exp-label">EastWay</div></div>
  <p class="exp-desc">Virtual servers, network and CCTV upgrade design and project management for this landmark road transportation Public Private Partnership (PPP).</p>
</div>
<div class="abs exp-card" style="left:612px">
  <div class="exp-img" role="img" aria-label="Black and white photo of a hospital building"><div class="exp-label">Parkside Women's Hospital</div></div>
  <p class="exp-desc">Security technology lifecycle consulting for this leading Health Care Public Private Partnership (PPP) which is operated by Hollis &amp; Grant.</p>
</div>
<div class="abs exp-card" style="left:862px">
  <div class="exp-img" role="img" aria-label="Black and white photo of an office tower"><div class="exp-label">Meridian Towers</div></div>
  <p class="exp-desc">Shared building network and security systems integration consulting for this iconic office tower which is managed by Varro Property.</p>
</div>

<!-- Footer -->
<div class="abs footer"></div>
<div class="abs brand" style="left:112px;top:3478px"><span class="dot"></span>PELU</div>
<div class="abs social" style="left:112px;top:3600px">Social</div>
<div class="abs social" style="left:180px;top:3600px">Network</div>

<div class="abs foot-head" style="left:388px">VISIT US</div>
<div class="abs foot-line" style="left:388px"></div>
<svg class="abs" style="left:390px;top:3506px" width="14" height="19" viewBox="0 0 14 19" fill="#d7261e"><path d="M7 0a7 7 0 0 1 7 7c0 5-7 12-7 12S0 12 0 7a7 7 0 0 1 7-7z"/><circle cx="7" cy="7" r="2.5" fill="#1b1819"/></svg>
<p class="abs foot-text" style="left:421px;top:3501px">Pelu<br>GPO Box 4120<br>MELBOURNE VIC 3001</p>

<div class="abs foot-head" style="left:662px">CONTACT US</div>
<div class="abs foot-line" style="left:662px"></div>
<svg class="abs" style="left:663px;top:3508px" width="17" height="17" viewBox="0 0 24 24" fill="#d7261e"><path d="M6.6 10.8a15 15 0 0 0 6.6 6.6l2.2-2.2a1 1 0 0 1 1-.25 11.4 11.4 0 0 0 3.6.57 1 1 0 0 1 1 1V20a1 1 0 0 1-1 1A17 17 0 0 1 3 4a1 1 0 0 1 1-1h3.5a1 1 0 0 1 1 1c0 1.25.2 2.45.57 3.57a1 1 0 0 1-.25 1z"/></svg>
<p class="abs foot-text" style="left:698px;top:3503px">1300 555 019</p>
<svg class="abs" style="left:663px;top:3547px" width="17" height="13" viewBox="0 0 17 13" fill="#d7261e"><rect width="17" height="13" rx="1"/><path d="M1 1l7.5 6L16 1" stroke="#1b1819" stroke-width="1.5" fill="none"/></svg>
<p class="abs foot-text" style="left:698px;top:3539px">hello@pelu.com.au</p>

<div class="abs foot-head" style="left:982px">QUICK LINKS</div>
<div class="abs foot-line" style="left:982px"></div>
<p class="abs foot-text" style="left:982px;top:3503px">Home<br>Experience<br>Services<br>Team<br>About<br>Contact</p>

<div class="abs" style="left:376px;top:3615px;width:562px;height:1px;background:#8a8584"></div>
<p class="abs foot-text" style="left:370px;top:3646px;font-size:17px">2023 Pelu. All Rights Reserved.</p>

</body>
</html>
```